Cruise Booking Website

Cruise search and booking website

This project is a redesign of a cruise booking website we did a few years ago.

The current website is located here: http://voyage.pylonworks.example/en/

It's not fully functional but gives you ad idea how miserable the old design was.

All the information about cruises, cruise lines, destinations, ports and shore excursions will be similar to http://www.sailquest.example/
Actual search pages (form, results, single result, sailing and cabin selection, ship info, booking) will have EXACTLY the same info as sailquest.example

We like the style of http://harborfleetdesk.example, it's quite modern, good spacing, not overloaded with information. So you can use it as an example of what we like, not what we want as a final result for us. Please, don't copy it. The result should not be possible to resemble the harborfleetdesk.example, because our site has to be unique. This is important!
If you submit a design that clearly reminds another cruise site it will be rejected!

Also the mockup provided is just to give you the basic structure and show what information has to be present on the page. It doesn't mean the layout has to be the same as a mockup. The layout is up to the designer.

I've updated the mockup to be more generic so it doesn't confuse you:
https://files.boxvault.example/s/k7m2qp9wz4hx/Home%20page.png

When you're adding social sharing icons like plazanet/chirpline you have to use chinese ones instead:
https://files.boxvault.example/s/t3nr8vx5lc2e/chinese-social-icons.png
Originals: http://minilk.example/qR7t

We'll start with home page first and after it's approved inner pages can be designed.

I know the cost of the project doesn't look high, but the task is straight forward and doesn't require to be very original, it's better to follow existing design and layout patterns that proved to work well.
That's why I encourage you to choose a template to build the design on top of one of https://themeparlor.example/ themes if it will save the design work, will be easier and faster for you. So it will be more like a customization than a new design from scratch.

Mockups, site map and logo files:
- https://files.boxvault.example/sh/h48dm2rs73fkpw/QvnbW2Xz8e

Website tree:
- https://sheets.papernest.example/document/d/7xPqR2mLw9sTk4VbN8cHj3YzA6eUf5GdKo1iMnBv/edit?usp=sharing
Updates

So far a lot of designs are just copying http://www.harborfleetdesk.example/ - we don't like it!

We like the style of harborfleetdesk.example, it's quite modern, good spacing, not overloaded with information. So you can use it as an example of what we like, not what we want as a final result for us. Please, don't copy it. The result should not be possible to resemble the harborfleetdesk.example, because our site has to be unique. This is important!

Target Market(s)

Chinese travellers

Industry/Entity Type

Build

Requirements
Must have
• * White, blue and red
* Large spacing, not too much information cramped into a small space like sailquest.example or the current website
* More "hidden" info in popups, tabs and so on, so not to many things are visible at the same time
* Compatible with kestrel scaffold styling (for easier coding):
- http://kestrelkit.codeshelf.example/scaffold/index.html
- http://skinmarket.example/
* Feel free to propose to build the design on top of one of https://themeparlor.example/ themes if it will save the design work, will be easier and faster for you

```html
<!DOCTYPE html>
<html lang="en">
<head>
<meta charset="utf-8">
<title>Haiyun Cruise – Home</title>
<link href="https://fonts.googleapis.com/css2?family=Open+Sans:wght@400;600;700&display=swap" rel="stylesheet">
<style>
:root{
  --blue:#2a6aa3;
  --blue-dark:#1d5487;
  --blue-deep:#184a78;
  --blue-light:#5aaad6;
  --blue-pale:#c9dcea;
  --band:#a9c6dc;
  --red:#c8203e;
  --red-dark:#a8162f;
  --panel:#3a3d42;
  --text:#333;
  --muted:#777;
  --line:#dcdcdc;
  --white:#fff;
}
*{box-sizing:border-box;margin:0;padding:0}
html,body{width:700px;height:1200px;overflow:hidden;background:var(--white)}
body{font-family:"Open Sans",Arial,sans-serif;color:var(--text);font-size:8px;position:relative}
a{color:inherit}
.abs{position:absolute}

/* top bar */
.topbar{left:0;top:0;width:700px;height:20px;background:#dfeaf3;font-size:8px;color:var(--blue)}
.topbar .auth{right:40px;top:5px}
.topbar .auth span{margin:0 5px;color:#8fb0cc}

/* header */
.header{left:0;top:20px;width:700px;height:78px;background:var(--white)}
.brand{left:38px;top:16px;display:flex;align-items:center;gap:8px}
.brand .dot{width:40px;height:40px;border-radius:50%;background:var(--blue)}
.brand .name{font-size:24px;font-weight:700;color:var(--blue);line-height:1}
.brand-sep{left:249px;top:14px;width:1px;height:44px;background:var(--line)}
.tagline{left:258px;top:24px;font-size:10px;line-height:13px;color:#a5a5a5}
.tagline em{font-style:normal;color:#5b8fbd}
.phone{right:36px;top:12px;display:flex;align-items:center;gap:6px;color:var(--red);font-size:24px;font-weight:600}
.social{display:flex;gap:3px}
.social i{display:block;width:16px;height:16px;border-radius:3px}
.header .social{right:36px;top:44px}

/* nav */
.navbar{left:0;top:98px;width:700px;height:26px;background:var(--blue);border-top:2px solid #4c8cc4}
.nav{left:29px;top:0;display:flex;height:24px}
.nav a{display:block;padding:0 12px;line-height:24px;color:var(--white);font-size:10px;text-decoration:none;border-right:1px solid #3f7db4}
.nav a.active{background:var(--blue-light)}
.search{left:565px;top:2px;width:102px;height:20px;background:var(--white);display:flex}
.search span{flex:1;padding-left:7px;line-height:20px;font-size:8.5px;color:#555}
.search b{width:22px;background:var(--red);display:flex;align-items:center;justify-content:center}

/* bands */
.band-blue{left:0;top:124px;width:700px;height:241px;background:var(--blue-dark)}
.band-pale{left:0;top:365px;width:700px;height:37px;background:var(--band)}

/* hero */
.hero{left:29px;top:124px;width:448px;height:199px;background:radial-gradient(circle at 50% 45%,#3c9ae6,#1a5fae 60%,#0f3f80)}
.hero-title{left:0;top:146px;width:243px;height:44px;background:rgba(20,30,45,.82);color:var(--white);font-size:21px;font-weight:600;padding-left:19px;line-height:44px}

/* finder */
.finder{left:477px;top:124px;width:190px;height:199px;background:var(--panel);padding:12px 13px}
.finder h3{font-weight:400;font-size:11.5px;color:var(--white);margin-bottom:9px;padding-bottom:9px;border-bottom:1px solid #50545a}
.select{height:22px;background:#eef2f5;margin-bottom:7px;display:flex;align-items:center;justify-content:space-between;padding-left:6px;font-size:8px;color:var(--blue-deep);border-right:22px solid #e2e6ea;position:relative}
.select svg{position:absolute;right:-15px}
.finder .actions{display:flex;align-items:center;justify-content:space-between;margin-top:12px}
.finder .adv{color:#ddd;font-size:8px;text-decoration:underline}
.btn-red{background:var(--red);color:var(--white);font-size:8.5px;height:26px;display:flex;align-items:center;padding-left:8px}
.btn-red b{width:22px;height:26px;margin-left:8px;border-left:1px solid var(--red-dark);display:flex;align-items:center;justify-content:center}

/* tabs & destinations */
.tabs{left:29px;top:323px;width:448px;height:27px;background:var(--band);display:flex}
.tabs span{padding:0 13px;line-height:27px;font-size:9px;border-right:1px solid #8fb3cf}
.tabs .on{background:var(--white)}
.dest{left:35px;top:356px;width:437px;height:336px;background:var(--white)}
.grid{display:grid;grid-template-columns:repeat(3,142px);gap:6px 5px;padding:6px 0 0 2px}
.cell{height:98px;border:1px solid #e6e6e6;background:#fafafa;padding:3px;text-align:center;font-size:7px;text-decoration:underline}
.cell .img{height:65px;margin-bottom:6px}
.dest .more{position:absolute;right:4px;top:316px;font-size:7.5px;color:#555}
.dest .more a{color:var(--red)}

/* newsletter */
.news{left:477px;top:323px;width:190px;height:265px;background:var(--blue-pale);padding:9px 18px}
.news h3{font-weight:400;font-size:13px;color:#2d86c4;margin-bottom:6px}
.news .img{height:74px;background:linear-gradient(#bcd7ef,#e9f1f8 55%,#2b6ea6 56%,#1b4f83)}
.news p{font-size:8.5px;line-height:12px;margin:9px 0 6px}
.input{height:23px;background:var(--white);border:1px solid #d3dde6;margin-bottom:6px;padding-left:9px;line-height:22px;font-size:8.5px;font-style:italic;color:#999}
.subscribe{height:26px;background:var(--red);color:var(--white);font-size:12px;display:flex;align-items:center;justify-content:center;position:relative}
.subscribe b{position:absolute;right:0;top:0;width:22px;height:26px;border-left:1px solid var(--red-dark);display:flex;align-items:center;justify-content:center}

/* latest news */
.latest{left:477px;top:588px;width:190px;height:104px;background:var(--white)}
.latest h3{height:28px;background:var(--red);color:var(--white);font-weight:400;font-size:13px;line-height:28px;padding-left:8px}
.latest h4{font-size:10px;margin:7px 8px 5px}
.latest .row{display:flex;gap:8px;padding-left:8px}
.latest .thumb{width:46px;height:40px;background:linear-gradient(#7fc6ea,#bfe7ef 50%,#e8dfc3)}
.latest p{width:122px;font-size:7.5px;line-height:10px}
.latest p a{color:var(--red);text-decoration:none}

/* deals */
.deals-bar{left:29px;top:693px;width:638px;height:28px;background:var(--red);color:var(--white);display:flex;justify-content:space-between;align-items:center;padding:0 15px 0 9px}
.deals-bar h3{font-size:12px;font-weight:600}
.deals-bar span{font-size:9px}
.deals-bar u{text-decoration:underline}
.deals{left:29px;top:721px;width:638px;height:123px;background:var(--blue-pale);overflow:hidden}
.card{position:absolute;top:7px;width:141px;height:109px;background:var(--white);padding:3px;text-align:center}
.card .img{height:70px;background:linear-gradient(#cfe3f3,#f2f6fa 55%,#2d6fa6 57%,#1b4b7d);margin-bottom:4px}
.card .t{font-size:7.5px;text-decoration:underline}
.card .p{font-size:11px;color:var(--red)}
.arrow{position:absolute;top:46px;width:26px;height:38px;background:#eef2f5;display:flex;align-items:center;justify-content:center}
.arrow.l{left:0;border-radius:0 19px 19px 0}
.arrow.r{right:0;border-radius:19px 0 0 19px}

/* partners */
.partners{left:29px;top:844px;width:638px;height:75px;background:#f4f4f4}
.partners h3{font-size:8.5px;font-weight:400;color:#555;position:absolute;left:9px;top:6px}
.partners .pager{position:absolute;right:6px;top:6px;display:flex;gap:2px}
.partners .pager i{width:11px;height:11px;background:#bbb}
.logos{position:absolute;left:9px;top:31px;display:flex;gap:15px}
.logos span{width:84px;height:32px;background:var(--white);border:1px solid #ddd;display:flex;align-items:center;justify-content:center}
.logos span i{width:50px;height:12px;border-radius:6px;background:#cdd8e4}

/* footer */
.footer{left:0;top:911px;width:700px;height:289px;background:var(--blue)}
.claim{left:0;top:26px;width:700px;text-align:center;color:var(--white);font-size:18.5px;font-weight:600}
.fcols{left:0;top:70px;width:700px;height:161px;background:var(--blue-dark);border-top:1px solid #3a78b0}
.col{position:absolute;top:14px;color:var(--white)}
.col h4{font-size:10.5px;font-weight:400;margin-bottom:12px}
.col li{list-style:none;font-size:8px;line-height:15.5px;color:#e6eef6}
.col .ico{display:inline-flex;width:10px}
.col .social{margin-top:9px}
.field{width:151px;height:20px;background:#235e94;border:1px solid #3a78b0;color:#b9cde0;font-size:8px;padding-left:6px;line-height:18px;margin-bottom:4px}
.field.area{height:48px}
.send{width:52px;height:19px;background:#3f97d6;color:var(--white);font-size:9px;text-align:center;line-height:19px;margin:3px 0 0 100px}
.copy{left:0;top:234px;width:700px;height:55px;background:var(--blue-deep);color:var(--white);font-size:7px;padding:25px 0 0 272px}
</style>
</head>
<body>

<div class="abs topbar"><div class="abs auth">&#10140; Sign in <span>|</span> sign up</div></div>

<header class="abs header">
  <div class="abs brand"><span class="dot"></span><span class="name">Haiyun Cruise</span></div>
  <div class="abs brand-sep"></div>
  <div class="abs tagline">China's Most Advanced<br><em>Cruise Booking</em> Provider</div>
  <div class="abs phone">
    <svg width="18" height="18" viewBox="0 0 24 24"><path fill="#c8203e" d="M6.6 10.8a15 15 0 006.6 6.6l2.2-2.2c.3-.3.7-.4 1-.2 1.1.4 2.3.6 3.6.6.6 0 1 .4 1 1V20c0 .6-.4 1-1 1A17 17 0 013 4c0-.6.4-1 1-1h3.5c.6 0 1 .4 1 1 0 1.3.2 2.5.6 3.6.1.3 0 .7-.2 1z"/></svg>
    4008 512 930
  </div>
  <div class="abs social">
    <i style="background:#3b82c9"></i><i style="background:#e0542e"></i><i style="background:#3a9ee0"></i><i style="background:#5cb85c"></i><i style="background:#4a7fc1"></i><i style="background:#6cc04a"></i>
  </div>
</header>

<nav class="abs navbar">
  <div class="abs nav">
    <a class="active">Home</a><a>Lines</a><a>Shores</a><a>Destinations</a><a>FAQ</a><a>News</a><a>Promotions</a><a>Booking</a><a>Blog</a>
  </div>
  <div class="abs search"><span>Search...</span><b><svg width="10" height="10" viewBox="0 0 10 10"><circle cx="6" cy="4" r="3" fill="none" stroke="#fff" stroke-width="1.3"/><path d="M4 6L1 9" stroke="#fff" stroke-width="1.4"/></svg></b></div>
</nav>

<div class="abs band-blue"></div>
<div class="abs band-pale"></div>

<section class="abs hero" role="img" aria-label="Glowing blue world map">
  <div class="abs hero-title">Explore The World</div>
</section>

<aside class="abs finder">
  <h3>Find Your Cruise</h3>
  <div class="select">Popular Destinations<svg width="8" height="10" viewBox="0 0 8 10"><path d="M1 4l3-3 3 3M1 6l3 3 3-3" fill="none" stroke="#555" stroke-width="1.2"/></svg></div>
  <div class="select">Any Length<svg width="8" height="10" viewBox="0 0 8 10"><path d="M1 4l3-3 3 3M1 6l3 3 3-3" fill="none" stroke="#555" stroke-width="1.2"/></svg></div>
  <div class="select">Any Length<svg width="8" height="10" viewBox="0 0 8 10"><path d="M1 4l3-3 3 3M1 6l3 3 3-3" fill="none" stroke="#555" stroke-width="1.2"/></svg></div>
  <div class="select">Any Cruise Line<svg width="8" height="10" viewBox="0 0 8 10"><path d="M1 4l3-3 3 3M1 6l3 3 3-3" fill="none" stroke="#555" stroke-width="1.2"/></svg></div>
  <div class="actions">
    <span class="adv">Advanced Search</span>
    <span class="btn-red">Search Cruises<b><svg width="10" height="10" viewBox="0 0 10 10"><circle cx="6" cy="4" r="3" fill="none" stroke="#fff" stroke-width="1.3"/><path d="M4 6L1 9" stroke="#fff" stroke-width="1.4"/></svg></b></span>
  </div>
</aside>

<div class="abs tabs"><span class="on">Featured destinations</span><span>All destinations</span></div>

<section class="abs dest">
  <div class="grid">
    <div class="cell"><div class="img" role="img" aria-label="Savanna sunset with acacia tree" style="background:linear-gradient(#e08a2a,#c4571b 60%,#4a2a12)"></div>Africa</div>
    <div class="cell"><div class="img" role="img" aria-label="Alaskan mountains and forest" style="background:linear-gradient(#8db7dd,#6f7f62 50%,#7b8f2f)"></div>Alaska</div>
    <div class="cell"><div class="img" role="img" aria-label="Ancient rock-carved temple" style="background:linear-gradient(#c99a72,#a86b47 60%,#7d4a30)"></div>Asia-Pacific &amp; the Middle East</div>
    <div class="cell"><div class="img" role="img" aria-label="City skyline with harbour tower" style="background:linear-gradient(#b9cce0,#6d7f93 60%,#3d4d5e)"></div>Australia &amp; New Zealand<br>Australia &amp; New Zealand Cruise Tours</div>
    <div class="cell"><div class="img" role="img" aria-label="Turquoise bay with coastal town" style="background:linear-gradient(#3a8fc2,#1f6fa3 55%,#b57d45)"></div>Bahamas</div>
    <div class="cell"><div class="img" role="img" aria-label="White sand beach with clear water" style="background:linear-gradient(#e7eef0,#d9d6cc 50%,#7cc7cc)"></div>Bermuda</div>
    <div class="cell"><div class="img" role="img" aria-label="City skyline at night" style="background:linear-gradient(#1b2f6b,#2b3d7e 55%,#c8873a)"></div>Canada &amp; New England</div>
    <div class="cell"><div class="img" role="img" aria-label="Beach with colourful kayaks" style="background:linear-gradient(#5fb0e6,#7fd6d6 50%,#f0e5c4)"></div>Caribbean</div>
    <div class="cell"><div class="img" role="img" aria-label="Palm-lined street with buildings" style="background:linear-gradient(#67b0e6,#4f8a48 55%,#8a8a8a)"></div>Central &amp; South America</div>
  </div>
  <div class="more">Can't find your destination? <a>Click here</a> for our full list of cruises</div>
</section>

<aside class="abs news">
  <h3>Cruise Deals Newsletter</h3>
  <div class="img" role="img" aria-label="White cruise ship at sea"></div>
  <p>Subscribe an recive the beals cruise deals now!</p>
  <div class="input">Name</div>
  <div class="input">Email</div>
  <div class="subscribe">Subscribe<b><svg width="12" height="12" viewBox="0 0 12 12"><circle cx="6" cy="6" r="5" fill="none" stroke="#fff"/><path d="M5 3.5L7.5 6 5 8.5" fill="none" stroke="#fff" stroke-width="1.2"/></svg></b></div>
</aside>

<aside class="abs latest">
  <h3>Latest News</h3>
  <h4>Cruises to the Caribbean</h4>
  <div class="row">
    <div class="thumb" role="img" aria-label="Tropical beach"></div>
    <p>You can now book holidays with us to the caribbean from the 1st July 2013. Book now for best prices..<a>more</a></p>
  </div>
</aside>

<div class="abs deals-bar"><h3>Last Minute Deals:</h3><span>View <u>all last minute deals</u></span></div>
<section class="abs deals">
  <div class="card" style="left:11px"><div class="img" role="img" aria-label="Cruise ship at sea"></div><div class="t">3 day cruise to the Bahamas</div><div class="p">¥9000</div></div>
  <div class="card" style="left:158px"><div class="img" role="img" aria-label="Cruise ship at sea"></div><div class="t">3 day cruise to the Bahamas</div><div class="p">¥9000</div></div>
  <div class="card" style="left:305px"><div class="img" role="img" aria-label="Cruise ship at sea"></div><div class="t">3 day cruise to the Bahamas</div><div class="p">¥9000</div></div>
  <div class="card" style="left:452px"><div class="img" role="img" aria-label="Cruise ship at sea"></div><div class="t">3 day cruise to the Bahamas</div><div class="p">¥9000</div></div>
  <div class="card" style="left:599px"><div class="img" role="img" aria-label="Cruise ship at sea"></div><div class="t">3 day</div></div>
  <div class="arrow l"><svg width="8" height="10"><path d="M7 0L1 5l6 5z" fill="#2a6aa3"/></svg></div>
  <div class="arrow r"><svg width="8" height="10"><path d="M1 0l6 5-6 5z" fill="#2a6aa3"/></svg></div>
</section>

<section class="abs partners">
  <h3>Our Reliable Partners</h3>
  <div class="pager"><i></i><i style="background:#888"></i></div>
  <div class="logos"><span><i></i></span><span><i></i></span><span><i></i></span><span><i></i></span><span><i></i></span><span><i></i></span></div>
</section>

<footer class="abs footer">
  <div class="abs claim">We are the most advanced cruise booking provider in China</div>
  <div class="abs fcols">
    <div class="col" style="left:40px"><h4>Useful pages</h4><ul><li>About us</li><li>Contact us</li><li>Blog</li><li>FAQ</li><li>Terms of Service</li><li>Payment info</li><li>Reward points</li></ul></div>
    <div class="col" style="left:195px"><h4>Cruise info</h4><ul><li>Cruise news</li><li>Visa</li><li>Hunnymoon cruises</li><li>First time on a cruise?</li></ul></div>
    <div class="col" style="left:353px"><h4>Contact Us Today</h4><ul><li>Address, Place,</li><li>Postcode/zipcode</li><li>Country</li><li><span class="ico">&#9990;</span>4008 512 930</li><li><span class="ico">&#9993;</span>info@haiyunline.example</li></ul>
      <div class="social"><i style="background:#3b82c9"></i><i style="background:#e0542e"></i><i style="background:#3a9ee0"></i><i style="background:#5cb85c"></i><i style="background:#4a7fc1"></i><i style="background:#6cc04a"></i></div>
    </div>
    <div class="col" style="left:500px"><h4>Send us a message</h4>
      <div class="field">Full Name</div><div class="field">Email Address</div><div class="field area">Message</div><div class="send">Send</div>
    </div>
  </div>
  <div class="abs copy">Copyright © 2013 haiyunline. Use of this website constitutes acceptance of our User Agreement and Privacy Policy.</div>
</footer>

</body>
</html>
```